Non fiction leadership Book Cover design needed for “Stay Bold: Build On Lasting Discipline”

I need a front cover design for a new book 6 X 9 traditional non-fiction book.

Title: "Stay BOLD - Build On Lasting Discipline"

The subtitle is not finalized- so use 2 lines of smaller dummy text

My brand guide is attached (please use the tan color sparingly)

I'd like to see BOLD look like it is in motion and "flying" across the page

Need CREATIVE designs and options

Do not want my picture on the front cover - I do want it on the back cover.

On the front cover I’d like to see creative use of font to create movement on “BOLD”

Target Market(s)

Business leaders

Industry/Entity Type

Aviation

Font styles to use
Other font styles liked:
• See style guide- can add additional font (modern script or san serif)

Colors
0054AA
0677BA
7BADD7
CADEEF
E8F1F8
EB3D1F
EC4F4E
F09395
F8D3D4
FCEDEE

Requirements
Must have
• Creative font use, using perspective to create movement/motion on BOLD
Should not have
• My picture on the front cover- my picture should be on the back cover

```html
<!DOCTYPE html>
<html lang="en">
<head>
<meta charset="utf-8">
<title>Stay BOLD - Build On Lasting Discipline</title>
<link rel="stylesheet" href="https://fonts.googleapis.com/css2?family=Bebas+Neue&family=Lobster&display=swap">
<style>
  :root {
    --sky-mist: #e8f1f8;
    --sky-pale: #cadeef;
    --sky-soft: #7badd7;
    --flight-blue: #0677ba;
    --deep-blue: #0054aa;
    --signal-red: #eb3d1f;
    --rose: #f09395;
    --tan-accent: #e3b98a;
  }
  html, body {
    margin: 0;
    padding: 0;
    width: 800px;
    height: 1200px;
    overflow: hidden;
    background: var(--sky-mist);
  }
  .cover {
    position: relative;
    width: 800px;
    height: 1200px;
    overflow: hidden;
    background: linear-gradient(180deg, var(--sky-mist) 0%, #ffffff 55%, var(--sky-mist) 100%);
    color: var(--deep-blue);
  }
  .title {
    margin: 0;
    font-family: "Lobster", cursive;
    font-weight: 400;
  }
  .title-line {
    position: absolute;
    left: 0;
    width: 800px;
    text-align: center;
    line-height: 1;
    white-space: nowrap;
    transform: rotate(-6deg);
  }
  .title-stay {
    top: 20px;
    font-size: 225px;
    letter-spacing: -4px;
  }
  .title-bold {
    top: 285px;
    padding-left: 120px;
    width: 680px;
    font-size: 140px;
    letter-spacing: 4px;
    color: var(--signal-red);
    transform-origin: 60% 50%;
    transform: perspective(500px) rotateY(-28deg) skewX(-14deg) rotate(-7deg);
    text-shadow: -10px 4px 0 var(--rose), -20px 8px 0 var(--sky-pale);
  }
  .speed-lines {
    position: absolute;
    top: 330px;
    left: 30px;
    width: 300px;
    height: 140px;
  }
  .title-build {
    top: 480px;
    font-size: 150px;
    letter-spacing: -2px;
  }
  .title-discipline {
    top: 725px;
    font-size: 82px;
    color: var(--flight-blue);
    transform: rotate(-5deg);
  }
  .subtitle {
    position: absolute;
    top: 932px;
    left: 0;
    width: 800px;
    margin: 0;
    text-align: center;
    font-family: "Bebas Neue", sans-serif;
    font-size: 40px;
    line-height: 60px;
    letter-spacing: 5px;
    font-weight: 400;
    color: var(--flight-blue);
  }
  .author-rule {
    position: absolute;
    top: 1080px;
    left: 340px;
    width: 120px;
    height: 4px;
    background: var(--tan-accent);
  }
  .author {
    position: absolute;
    top: 1105px;
    left: 0;
    width: 800px;
    margin: 0;
    text-align: center;
    font-family: "Bebas Neue", sans-serif;
    font-size: 62px;
    line-height: 1;
    letter-spacing: 6px;
    font-weight: 400;
    color: var(--deep-blue);
  }
</style>
</head>
<body>
  <main class="cover">
    <svg class="speed-lines" viewBox="0 0 300 140" aria-hidden="true">
      <g stroke-linecap="round" fill="none">
        <line x1="20" y1="40" x2="240" y2="18" stroke="#7badd7" stroke-width="6"/>
        <line x1="70" y1="70" x2="260" y2="52" stroke="#f09395" stroke-width="5"/>
        <line x1="0" y1="102" x2="250" y2="80" stroke="#0677ba" stroke-width="4"/>
        <line x1="110" y1="128" x2="270" y2="114" stroke="#cadeef" stroke-width="6"/>
      </g>
    </svg>
    <h1 class="title">
      <span class="title-line title-stay">Stay</span>
      <span class="title-line title-bold">BOLD</span>
      <span class="title-line title-build">Build On</span>
      <span class="title-line title-discipline">Lasting Discipline</span>
    </h1>
    <p class="subtitle">Unlock your inner potential<br>and soar to new heights</p>
    <div class="author-rule"></div>
    <p class="author">Author Name</p>
  </main>
</body>
</html>
```